RB Halden Electric Yard Sign

Looking to have a yard sign designed that we can place at projects we are working on. Most likely will be 18" H x 24" W but flexible that we can increase the size if necessary. It should include our logo, our phone # 609-555-0147, website rbhaldenelectric.example and slogan, built on integrity, driven by excellence. Colors should match our brand.

```html
<!DOCTYPE html>
<html lang="en">
<head>
<meta charset="utf-8">
<title>RB Halden Electric Yard Sign</title>
<link href="https://fonts.googleapis.com/css2?family=Montserrat:wght@600;800&family=Barlow+Condensed:ital,wght@1,600&display=swap" rel="stylesheet">
<style>
  :root {
    --bg: #4b4b4b;
    --sign: #ffffff;
    --red: #e0202e;
    --navy: #0d3560;
  }
  * { margin: 0; padding: 0; box-sizing: border-box; }
  html, body { width: 1200px; height: 1001px; overflow: hidden; background: var(--bg); }
  .yard-sign {
    position: absolute; left: 60px; top: 95px;
    width: 1080px; height: 810px;
    background: var(--sign);
  }
  .info-frame {
    position: absolute; left: 33px; top: 33px; right: 33px; height: 590px;
    border: 4px solid var(--red);
    display: flex; flex-direction: column; align-items: center;
    padding-top: 110px;
  }
  .brand-name {
    font-family: "Montserrat", sans-serif; font-weight: 800;
    font-size: 66px; color: var(--red); line-height: 1;
    text-transform: uppercase; letter-spacing: 1px;
  }
  .brand-descriptor {
    margin-top: 18px; padding-bottom: 8px;
    font-family: "Montserrat", sans-serif; font-weight: 600;
    font-size: 40px; color: var(--navy); letter-spacing: 6px; line-height: 1;
    border-bottom: 5px solid var(--red);
  }
  .phone {
    margin-top: 52px; display: flex; align-items: center; gap: 10px;
    font-family: "Montserrat", sans-serif; font-weight: 800;
    font-size: 88px; color: var(--navy); line-height: 1; letter-spacing: 2px;
  }
  .website {
    margin-top: 30px; display: flex; align-items: center; gap: 16px;
    font-family: "Montserrat", sans-serif; font-weight: 800;
    font-size: 46px; color: var(--navy); line-height: 1;
  }
  .slogan-band {
    position: absolute; left: 33px; right: 33px; top: 655px; height: 112px;
    background: var(--navy);
    display: flex; align-items: center; justify-content: center;
    border-bottom: 7px solid var(--red);
  }
  .slogan {
    font-family: "Barlow Condensed", sans-serif; font-style: italic; font-weight: 600;
    font-size: 62px; color: #ffffff; text-transform: uppercase; letter-spacing: 1px;
  }
</style>
</head>
<body>
  <div class="yard-sign">
    <div class="info-frame">
      <div class="brand-name">RB Halden Electric</div>
      <div class="brand-descriptor">Electrical Contractor</div>
      <div class="phone">
        <svg width="48" height="60" viewBox="0 0 24 30" aria-hidden="true">
          <path d="M7 2 L11 8 L8 11 Q10 18 15 22 L18 19 L23 24 L19 28 Q8 26 4 13 Q3 6 7 2 Z" fill="var(--red)"/>
        </svg>
        <span>609-555-0147</span>
      </div>
      <div class="website">
        <svg width="38" height="38" viewBox="0 0 24 24" aria-hidden="true" fill="none" stroke="var(--red)" stroke-width="2">
          <circle cx="12" cy="12" r="10"/>
          <ellipse cx="12" cy="12" rx="4.5" ry="10"/>
          <line x1="2" y1="12" x2="22" y2="12"/>
          <line x1="4" y1="7" x2="20" y2="7"/>
          <line x1="4" y1="17" x2="20" y2="17"/>
        </svg>
        <span>rbhaldenelectric.example</span>
      </div>
    </div>
    <div class="slogan-band">
      <span class="slogan">Built on integrity, driven by excellence</span>
    </div>
  </div>
</body>
</html>
```